Harwick + Pell Architect Marketing campaign for a morern fresh architecture cutting egde firm th...

To create en exciting template for our monthly newsletters to go out to all our clients via email. I have added a bit of an idea of what we like but not limited to..... we like a nice clean fresh look with lots of white space. I hve aslo added a sketch of the type of how we might layt it out - you may have a better idea. also the pics of the projects for the first issue (issue #1)We like the opening page like the attached brewlane had and replace the cup with apic of our building/office. Cant wait to see what you come up with.

Target Market(s)

young professionals

Industry/Entity Type

Architectural

Font styles to use
Serif

Colors

Designer to choose colors to be used in the design.

Requirements
Must have
• Logo, text information provided, photos provided
Nice to have
• lots of white space, clean and frest looking

```html
<!DOCTYPE html>
<html lang="en">
<head>
<meta charset="utf-8">
<title>Harwick + Pell Architecture — Newsletter Issue #1</title>
<link href="https://fonts.googleapis.com/css2?family=Poppins:wght@400;500;700;800&display=swap" rel="stylesheet">
<style>
  :root {
    --ink: #2b2b2b;
    --white: #ffffff;
    --panel: #f2f2f2;
    --dark: #262626;
    --hero-blue: #6f87d8;
    --hero-blue-deep: #5b74c9;
    --badge-navy: #1f2f6b;
    --badge-grey: #8b8f95;
  }
  * { margin: 0; padding: 0; box-sizing: border-box; }
  html, body { width: 1200px; height: 4437px; overflow: hidden; background: var(--white); }
  body { position: relative; font-family: 'Poppins', sans-serif; color: var(--ink); }
  .abs { position: absolute; }

  .brand { left: 0; width: 1200px; top: 30px; display: flex; flex-direction: column; align-items: center; }
  .brand-row { display: flex; align-items: center; gap: 14px; }
  .brand-square { width: 46px; height: 46px; border: 7px solid var(--ink); }
  .brand-name, .brand-sub { font-weight: 700; color: var(--ink); letter-spacing: 2px; }
  .brand-name { font-size: 34px; }
  .brand-sub { font-size: 14px; letter-spacing: 9px; margin-top: 6px; }

  .hero { left: 0; top: 189px; width: 1200px; height: 520px; background: var(--hero-blue); overflow: hidden; }
  .hero-photo { position: absolute; left: 520px; top: 0; width: 680px; height: 520px;
    background: linear-gradient(90deg, var(--hero-blue) 0%, #7e88a8 18%, #5a4038 45%, #6b3e2e 70%, #4a2d24 100%); }
  .hero-title { position: absolute; left: 34px; top: 90px; font-size: 66px; font-weight: 700; line-height: 74px; color: var(--white); }
  .hero-copy { position: absolute; left: 34px; top: 260px; width: 560px; font-size: 21px; line-height: 40px; color: var(--white); }

  .welcome { left: 34px; top: 745px; width: 1132px; height: 510px; background: var(--panel); text-align: center; }
  .welcome h2 { margin-top: 50px; font-size: 42px; font-weight: 700; letter-spacing: 1px; }
  .welcome p { font-size: 23px; line-height: 45px; margin-top: 18px; padding: 0 50px; }
  .welcome .lead { font-weight: 700; line-height: 40px; margin-top: 26px; padding: 0 160px; }

  .section-title { font-size: 43px; font-weight: 700; letter-spacing: .5px; line-height: 1; }
  .section-sub { font-size: 22px; margin-top: 28px; letter-spacing: .3px; }
  .section-copy { font-size: 23px; line-height: 45px; margin-top: 38px; }

  .drawing { left: 34px; top: 1378px; width: 650px; }
  .ph { position: absolute; }
  .ph-dusk-a { left: 751px; top: 1324px; width: 415px; height: 289px; background: linear-gradient(180deg, #6f8fb8 0%, #9fb2c6 45%, #4f6b3e 70%, #3d5530 100%); }
  .ph-dusk-b { left: 751px; top: 1629px; width: 415px; height: 287px; background: linear-gradient(180deg, #2f4b86 0%, #4d6ea6 35%, #2a2a2e 60%, #1c1c1e 100%); }

  .construction { left: 34px; top: 1978px; width: 1132px; height: 883px; background: var(--panel); }
  .ph-build-a { left: 34px; top: 2038px; width: 415px; height: 357px; background: linear-gradient(180deg, #b9bfc6 0%, #a9aeb4 40%, #4d4d50 70%, #6a6a6a 100%); }
  .ph-build-b { left: 34px; top: 2416px; width: 415px; height: 354px; background: linear-gradient(180deg, #b4bac1 0%, #a2a8ae 35%, #3d3d40 70%, #666 100%); }
  .construction-text { left: 489px; top: 2036px; width: 670px; }

  .feature-panel { left: 34px; top: 2951px; width: 350px; height: 1004px; background: var(--dark); color: var(--white); text-align: center; display: flex; flex-direction: column; justify-content: center; }
  .feature-panel h2 { font-size: 43px; font-weight: 700; line-height: 50px; }
  .feature-panel p { font-size: 22px; line-height: 38px; margin-top: 26px; }
  .ph-factory-a { left: 393px; top: 2951px; width: 308px; height: 491px; background: linear-gradient(180deg, #5a5f86 0%, #8b8aa8 40%, #2f2f33 70%, #444 100%); }
  .ph-factory-b { left: 393px; top: 3466px; width: 308px; height: 489px; background: linear-gradient(180deg, #54597f 0%, #8c88a6 45%, #2b2b2f 72%, #4a4a4a 100%); }
  .feature-copy { left: 727px; top: 2945px; width: 440px; font-size: 23px; line-height: 45px; }

  .social { left: 0; top: 4034px; width: 1200px; height: 188px; background: var(--dark); color: var(--white); text-align: center; }
  .social h3 { margin-top: 42px; font-size: 28px; font-weight: 700; letter-spacing: 1px; }
  .social-links { display: flex; justify-content: center; gap: 34px; margin-top: 24px; font-size: 20px; }

  .badge-a { left: 365px; top: 4280px; width: 232px; height: 90px; background: var(--badge-navy); border-radius: 6px; }
  .badge-b { left: 677px; top: 4270px; width: 155px; height: 112px; background: var(--badge-grey); border-radius: 6px; }
</style>
</head>
<body>

<header class="brand abs">
  <div class="brand-row"><span class="brand-square"></span><span class="brand-name">HARWICK + PELL</span></div>
  <span class="brand-sub">ARCHITECTURE</span>
</header>

<section class="hero abs">
  <div class="hero-photo" role="img" aria-label="Photo of the studio's timber-clad office building with signage"></div>
  <h1 class="hero-title">We’re glad<br>you’re here</h1>
  <p class="hero-copy">Now that you are a Harwick + Pell Architecture insider you’ll be among the first to hear about upcoming projects that the studio is working on, completed projects, news and more.</p>
</section>

<section class="welcome abs">
  <h2>WELCOME</h2>
  <p>It appears that there are a lot of people are genuinely interested in the building and construction industry, and we here at Harwick + Pell Architecture often get asked “what we are up to” and “what cool projects have we got on the go”. With that being said we thought we would share with you some of our projects at various stages for you all to enjoy.</p>
  <p class="lead">We plan on keeping you all up to date on what the studio is up to with monthly newsletters.</p>
</section>

<section class="drawing abs">
  <h2 class="section-title">ON THE DRAWING BOARD</h2>
  <p class="section-sub">LAKE ARDEN HOUSE // RESIDENTIAL</p>
  <p class="section-copy">We have recently completed this two story house concept overlooking the canals at Lake Arden here in Ashdale. We are currently in the Working Drawing phase at present. This house will stand out from the crowd and has a mixture of cedar, standing seam wall cladding and precast concrete panels. We are really excited to see this project to progress to construction. We will keep you posted on this one!</p>
</section>
<div class="ph ph-dusk-a" role="img" aria-label="Render of the two storey lakeside house with gardens"></div>
<div class="ph ph-dusk-b" role="img" aria-label="Dusk render of the house with lit glazing"></div>

<div class="construction abs"></div>
<div class="ph ph-build-a" role="img" aria-label="Site photo of the commercial building under construction"></div>
<div class="ph ph-build-b" role="img" aria-label="Site photo of the building facade with scaffolding"></div>
<section class="construction-text abs">
  <h2 class="section-title">UNDER CONSTRUCTION</h2>
  <p class="section-sub">KESWICK STREET – STAGE 1 // COMMERCIAL</p>
  <p class="section-copy" style="font-size:22.5px">This new development currently being construction by Larkin Commercial in Rowanvale is the anchor development for Keswick Street and the beginning of the reconfiguration / upgrade of the Rowanvale Town Centre. This is part of a major redevelopment for Rowanvale. We have worked closely with the Merrow District Council and surrounding residential neighbours so that new development benefits all involved. The building is fully tenanted with Grey Bean Coffee, Jade Dish Chinese Restaurant, Spice Lane Restaurant, Cellar Corner, Thread Works Clothing Store and a small dairy. Tenants are currently completing fit-outs for the spaces and the project is fast nearing completion and will be open for business in the next few months.</p>
</section>

<section class="feature-panel abs">
  <h2>FEATURE<br>PROJECT</h2>
  <p>KEYSTONE CUTTING &amp;<br>PROCESSING LTD //<br>COMMERCIAL</p>
</section>
<div class="ph ph-factory-a" role="img" aria-label="Dusk photo of the office entrance with black-framed glazing"></div>
<div class="ph ph-factory-b" role="img" aria-label="Dusk photo of the office and factory exterior"></div>
<p class="feature-copy abs">This new office and factory located in the new Ashdale Business Park is comprised of a large Cutting and Processing facility for the manufacturer of steel plate profiles. The facility 1,500m² houses two 10-tonne gantry cranes running the full length of the 60 x 25 metre workshop and was designed with the emphasis on maximum plate storage and profile cutting efficiency. Alongside the processing facility is an attached 238m² modern single level office building has been designed to project the character and brand of Keystone Cutting and to sit within the context of the Business Park. The interior fit-out uses a limited palette of materials to create a modern uncluttered interior.</p>

<footer class="social abs">
  <h3>STAY CONNECTION WITH US</h3>
  <div class="social-links"><span>Pagebook</span><span>Snapgram</span><span>Homeboard</span></div>
</footer>

<div class="abs badge-a" role="img" aria-label="Industry association membership badge"></div>
<div class="abs badge-b" role="img" aria-label="Professional member badge"></div>

</body>
</html>
```